Bench Advertisement - We Buy Houses Design Needed

Need a catchy, simple but elegant design for bus benches to advertise our company.

We need our website, or phone number, and a smal description (1-2 bulletpoints of what we do and what we offer)

The tricky part is for the designer to fit everything and make the website name as part of the title and fitting everything so that people passing by on the street can see what we offer.

Our website is quickdealhomebuyer.com - (916) 555-0143

Something simple but something that catches the eye of walking pedestrians, and drivers driving by the bench.

Our company buys houses, any condition, any situation, we buy houses for cash and close quickly. You can use this description to create a few bulletpoints however you like. Must follow dimensions in attachment.

Target Market(s)

People in foreclosure, about to lose their homes, people that need a quick cash sale of their property

Industry/Entity Type

Real Estate

Requirements
Must have
• catchy, website name, phone number, few brief bulletpoints about what we offer, colors that will catch peoples eye while walking or driving - advertisement will be placed on bus benches - visit our website to see the type of houses we buy - Also have more work for winner of design with possible bonuses
Nice to have
• Feel free to use description or images on our website - make sure the description is just bullet points and it fits with the overall theme / size of the advertisement - Bold bright colors - put yourself in their shoes (if you were going through financial difficulties and about to lose your house to foreclosure or auction, what would you want to see to pick up the phone and call us for a quick sale of your house?) (or if you have a house that you are having a problem with, problem renters, unkept/beat up house, what would make you want to call us and sell your house to us?)

```html
<!DOCTYPE html>
<html lang="en">
<head>
<meta charset="utf-8">
<title>Quick Deal Home Buyer – Bench Advertisement</title>
<link rel="stylesheet" href="https://fonts.googleapis.com/css2?family=Fira+Sans:wght@300;400;500&display=swap">
<style>
  :root {
    --plum: #9b356b;
    --white: #ffffff;
    --photo-sky: #c9d6de;
    --photo-roof: #6b5149;
    --photo-wall: #8c4b36;
    --photo-board: #b9a58c;
    --photo-tarp: #2f6fb8;
  }
  * { margin: 0; padding: 0; box-sizing: border-box; }
  html, body { width: 1200px; height: 343px; overflow: hidden; background: var(--plum); }
  .bench-ad {
    position: relative;
    width: 1200px;
    height: 343px;
    background: var(--plum);
    color: var(--white);
    font-family: "Fira Sans", sans-serif;
  }
  .brand {
    position: absolute;
    left: 0; top: 0;
    width: 360px; height: 206px;
    display: flex; align-items: center; justify-content: center;
  }
  .brand-name {
    font-size: 15px;
    font-weight: 400;
    letter-spacing: 0.3px;
    color: var(--white);
    margin-top: 60px;
  }
  .hero-photo {
    position: absolute;
    left: 361px; top: 0;
    width: 817px; height: 206px;
    background: linear-gradient(180deg, var(--photo-sky) 0%, var(--photo-roof) 22%, var(--photo-wall) 45%, var(--photo-board) 60%, var(--photo-tarp) 75%, var(--photo-wall) 100%);
  }
  .headline {
    position: absolute;
    left: 20px; top: 222px;
    width: 712px;
    text-align: center;
    font-size: 27.5px;
    font-weight: 300;
    line-height: 31px;
  }
  .contact {
    position: absolute;
    top: 297px;
    font-size: 19.5px;
    font-weight: 400;
    white-space: nowrap;
  }
  .contact-web { left: 40px; }
  .contact-phone { left: 455px; }
  .offer-list {
    position: absolute;
    left: 742px; top: 224px;
    width: 424px;
    list-style: none;
    font-size: 10px;
    font-weight: 300;
    line-height: 12px;
  }
  .offer-list li {
    position: relative;
    padding-left: 14px;
    margin-bottom: 11px;
    text-align: justify;
  }
  .offer-list li::before {
    content: "";
    position: absolute;
    left: 0; top: 3px;
    width: 6px; height: 6px;
    border-radius: 50%;
    background: var(--white);
  }
</style>
</head>
<body>
  <main class="bench-ad">
    <div class="brand">
      <span class="brand-name">QUICK DEAL HOME BUYER</span>
    </div>
    <div class="hero-photo" role="img" aria-label="Run-down single-storey house with boarded windows, a blue tarp over the entrance and debris in the yard"></div>

    <h1 class="headline">Our company buys houses, any condition, any situation,<br>we buy houses for cash and close quickly.</h1>

    <p class="contact contact-web">Visit now: quickdealhomebuyer.com</p>
    <p class="contact contact-phone">Call now : (916) 555-0143</p>

    <ul class="offer-list">
      <li>If you were going through financial difficulties and about to lose your house to foreclosure or auction, what would you want to see to pick up the phone and call us for a quick sale of your house?</li>
      <li>If you have a house that you are having a problem with, problem renters, unkept/beat up house,</li>
      <li>What would make you want to call us and sell your house to us?</li>
    </ul>
  </main>
</body>
</html>
```